Business Card for Brenwickpartners

Need to design a business card with attached logo

Target Market(s)

I'm a financial/Investment adviser so card must be professional

Industry/Entity Type

Business

Font styles to use
Serif
Sans Serif

Requirements
Must have
• Would like in include the GOLD version of my logo if possible

Tobin Brenwick
President

Address is
4127 Verlane Blvd
Ashcombe, Ca. 95999

Phone
555-555-0147
Fax
555-555-0183

Email
tobin@brenwickpartners.example

I also need the following tag line at the bottom of card:

Investment Advisor Representative of and Securities offered
through Halvern Capital Brokerage, LLC Member QUDEX, TRAB
and Registered Investment Advisor.

Nice to have
• Split color in order to incorporate GOLD LOGO
Should not have

```html
<!DOCTYPE html>
<html lang="en">
<head>
<meta charset="utf-8">
<title>Brenwick Partners — Business Card</title>
<link rel="stylesheet" href="https://fonts.googleapis.com/css2?family=Cinzel:wght@400;500&family=Arimo:wght@400&display=swap">
<style>
  :root {
    --bg: #6b6a68;
    --card-dark: #3a3a3b;
    --gold: #b8954a;
    --white: #ffffff;
    --ink: #1c1c1c;
    --muted: #d9d4c8;
  }
  * { box-sizing: border-box; margin: 0; padding: 0; }
  html, body {
    width: 1200px; height: 900px; overflow: hidden;
    background: var(--bg);
  }
  .canvas { position: relative; width: 1200px; height: 900px; }

  .card {
    position: absolute;
    height: 320px;
    box-shadow: 0 6px 18px rgba(0,0,0,.35);
    overflow: hidden;
  }

  /* Front */
  .card-front {
    left: 40px; top: 470px; width: 560px;
    background: var(--card-dark);
    display: flex; flex-direction: column; align-items: center; justify-content: center;
  }
  .brand { display: flex; align-items: center; gap: 16px; white-space: nowrap; }
  .brand-dot {
    width: 22px; height: 22px; border-radius: 50%;
    background: var(--gold); flex: none;
  }
  .brand-name {
    font-family: "Cinzel", serif; font-weight: 400;
    color: var(--gold); font-size: 38px; letter-spacing: 1px;
  }
  .front-tagline {
    margin-top: 14px;
    display: flex; align-items: center; gap: 12px;
    font-family: "Cinzel", serif; font-size: 13px; letter-spacing: 1.5px;
    color: var(--gold); white-space: nowrap;
  }
  .front-tagline .rule { width: 40px; height: 1px; background: var(--gold); }

  /* Back */
  .card-back {
    left: 600px; top: 120px; width: 580px;
    display: flex;
    background: var(--white);
  }
  .back-panel {
    width: 230px; height: 100%; flex: none;
    background: var(--card-dark);
    border-right: 3px solid var(--gold);
    padding: 26px 14px;
    display: flex; flex-direction: column; align-items: center;
    text-align: center;
  }
  .back-panel .brand { gap: 7px; }
  .back-panel .brand-dot { width: 10px; height: 10px; }
  .back-panel .brand-name { font-size: 15px; letter-spacing: .5px; }
  .back-subline {
    margin-top: 4px;
    font-family: "Cinzel", serif; font-size: 6px; letter-spacing: 1px;
    color: var(--gold); white-space: nowrap;
  }
  .person-name {
    margin-top: 18px;
    font-family: "Cinzel", serif; font-weight: 400; font-size: 16px; letter-spacing: .5px;
    white-space: nowrap;
  }
  .person-name .first { color: var(--gold); }
  .person-name .last { color: var(--white); }
  .person-title {
    margin-top: 2px;
    font-family: "Cinzel", serif; font-size: 12px; letter-spacing: 1px;
    color: var(--white);
  }
  .disclosure {
    margin-top: 26px;
    font-family: "Times New Roman", Times, serif; font-size: 10.5px; line-height: 1.35;
    color: var(--muted);
  }
  .back-contact {
    flex: 1;
    padding: 0 14px 30px 16px;
    display: flex; flex-direction: column; justify-content: flex-end;
    font-family: "Arimo", sans-serif; font-style: normal; font-size: 13px; line-height: 1.3;
    color: var(--ink); white-space: nowrap;
  }
</style>
</head>
<body>
<main class="canvas">

  <section class="card card-back" aria-label="Business card back">
    <div class="back-panel">
      <div class="brand">
        <span class="brand-dot"></span>
        <span class="brand-name">Brenwick Partners</span>
      </div>
      <p class="back-subline">RETIREMENT AND FINANCIAL SERVICES</p>
      <h1 class="person-name"><span class="first">TOBIN</span> <span class="last">BRENWICK</span></h1>
      <p class="person-title">PRESIDENT</p>
      <p class="disclosure">Investment Advisor Representative of and Securities offered through Halvern Capital Brokerage, LLC Member QUDEX, TRAB and Registered Investment Advisor.</p>
    </div>
    <address class="back-contact">
      <span>Address is 4127 Verlane Blvd Ashcombe, Ca. 95999</span>
      <span>Phone: 555-555-0147, Fax: 555-555-0183</span>
      <span>Email: tobin@brenwickpartners.example</span>
    </address>
  </section>

  <section class="card card-front" aria-label="Business card front">
    <div class="brand">
      <span class="brand-dot"></span>
      <span class="brand-name">Brenwick Partners</span>
    </div>
    <p class="front-tagline">
      <span class="rule"></span>
      <span>RETIREMENT AND FINANCIAL SERVICES</span>
      <span class="rule"></span>
    </p>
  </section>

</main>
</body>
</html>
```